Business Card Design Project

Doctor, Pain Management. Need a new business card design with appointment info on the back. New address is 18 Corvell Road, Suite 304, Brisdale, NJ 07391. Right now I believe the rest of the information is staying the same.

```html
<!DOCTYPE html>
<html lang="en">
<head>
<meta charset="utf-8">
<title>Steady Pain Management – Business Card</title>
<link rel="stylesheet" href="https://fonts.googleapis.com/css2?family=Libre+Baskerville:wght@400;700&family=Playfair+Display:wght@900&family=Open+Sans:wght@400;600&display=swap">
<style>
  :root{
    --ink:#0b0b0b;
    --yellow:#f2e84a;
    --title-yellow:#f3ec3c;
    --paper:#ffffff;
    --grey:#b9b9b9;
    --muted:#6d6d6d;
    --bg:#e4e4e4;
    --spine-a:#e0532a;
    --spine-b:#3a4250;
  }
  *{box-sizing:border-box;margin:0;padding:0}
  html,body{width:1200px;height:864px;overflow:hidden;background:var(--bg)}
  .canvas{position:relative;width:1200px;height:864px}
  .card{position:absolute;left:290px;width:620px;height:354px;background:var(--paper);overflow:hidden;box-shadow:0 4px 14px rgba(0,0,0,.18)}
  .card--front{top:40px}
  .card--back{top:470px}

  /* front */
  .front-art{position:absolute;inset:0}
  .brand-name{position:absolute;left:34px;top:44px;font-family:"Libre Baskerville",serif;font-weight:400;font-size:33px;color:var(--title-yellow);letter-spacing:.5px}
  .illustration{position:absolute;left:468px;top:110px;width:140px;height:140px;border-radius:50%;background:radial-gradient(circle at 50% 55%,var(--spine-a) 0 18%,var(--spine-b) 55%,transparent 72%)}
  .doctor{position:absolute;left:24px;top:196px;width:226px;text-align:right;font-family:"Libre Baskerville",serif}
  .doctor__name{font-weight:700;font-size:22px;color:var(--ink)}
  .doctor__creds{font-size:15px;color:var(--muted);margin-top:2px}
  .divider{position:absolute;left:258px;top:206px;width:1.5px;height:140px;background:var(--ink)}
  .contacts{position:absolute;left:270px;top:252px;list-style:none;font-family:"Open Sans",sans-serif;font-size:12.5px;color:var(--ink);line-height:16px}
  .contacts li{display:flex;align-items:flex-start;gap:6px}
  .icon{flex:none;width:11px;height:11px;margin-top:2.5px}
  .contacts .address{display:block;padding-left:17px}

  /* back */
  .back-art{position:absolute;inset:0}
  .appt-title{position:absolute;left:0;right:0;top:20px;text-align:center;font-family:"Playfair Display",serif;font-weight:900;font-size:28px;color:var(--ink)}
  .form{position:absolute;left:28px;right:28px;top:84px;font-family:"Libre Baskerville",serif;font-size:15px;color:var(--ink)}
  .field{display:flex;align-items:flex-end;gap:6px;margin-bottom:18px}
  .field__line{flex:1;border-bottom:1.2px solid var(--ink);height:14px}
  .days{display:flex;justify-content:space-between;margin-bottom:18px}
  .day{display:flex;align-items:center;gap:5px}
  .box{width:13px;height:13px;border:1.2px solid var(--ink)}
  .note{position:absolute;left:0;right:0;top:204px;text-align:center;font-family:"Libre Baskerville",serif;font-weight:700;font-size:13px;line-height:17px;color:var(--ink)}
  .back-contacts{position:absolute;top:272px;font-family:"Libre Baskerville",serif;font-size:13px;line-height:20px;color:var(--paper);list-style:none}
  .back-contacts--left{left:22px}
  .back-contacts--right{right:22px;text-align:right;top:296px}
  .back-contacts li{display:flex;align-items:center;gap:6px}
  .back-contacts--right li{justify-content:flex-end}
</style>
</head>
<body>
<main class="canvas">

  <section class="card card--front">
    <svg class="front-art" viewBox="0 0 620 354" width="620" height="354" aria-hidden="true">
      <path d="M0,146 C140,140 220,178 300,206 C380,236 440,262 620,262 L620,276 C440,276 380,250 300,222 C220,194 140,158 0,164 Z" fill="var(--grey)"/>
      <path d="M0,138 C140,130 220,170 300,198 C380,228 440,254 620,254 L620,264 C440,264 380,238 300,210 C220,182 140,146 0,152 Z" fill="var(--yellow)"/>
      <path d="M0,0 H620 V254 C440,254 380,228 300,198 C220,170 140,130 0,138 Z" fill="var(--ink)"/>
    </svg>
    <h1 class="brand-name">Steady Pain Management</h1>
    <div class="illustration" role="img" aria-label="Illustration of a person holding their lower back with the glowing spine highlighted"></div>
    <div class="doctor">
      <p class="doctor__name">Dr. Lin Harlow</p>
      <p class="doctor__creds">M.D., Ph.D.</p>
    </div>
    <div class="divider"></div>
    <ul class="contacts">
      <li><svg class="icon" viewBox="0 0 11 11"><rect width="11" height="11" fill="var(--ink)"/><path d="M3,2 L4.5,2 L5,4 L4,4.8 Q5,6.5 6.2,7 L7,6 L9,6.5 L9,8 Q5,9 2.5,4.5 Z" fill="#fff"/></svg>(973) 555-0148</li>
      <li><svg class="icon" viewBox="0 0 11 11"><rect width="11" height="11" fill="var(--ink)"/><rect x="2" y="4" width="7" height="4" fill="#fff"/><rect x="3.5" y="2" width="4" height="2" fill="#fff"/></svg>(973) 555.0162</li>
      <li><svg class="icon" viewBox="0 0 11 11"><rect width="11" height="11" fill="var(--ink)"/><rect x="2" y="3" width="7" height="5" fill="#fff"/><path d="M2,3 L5.5,6 L9,3" stroke="var(--ink)" fill="none" stroke-width=".8"/></svg>steadypmc.service@mailbox.com</li>
      <li><svg class="icon" viewBox="0 0 11 11"><rect width="11" height="11" fill="var(--ink)"/><circle cx="5.5" cy="5.5" r="3.2" fill="none" stroke="#fff" stroke-width="1"/><path d="M2.3,5.5 H8.7 M5.5,2.3 V8.7" stroke="#fff" stroke-width=".7"/></svg>www.steadypm.com</li>
      <li><svg class="icon" viewBox="0 0 11 11"><rect width="11" height="11" fill="var(--ink)"/><path d="M5.5,9 L3,5 A2.6,2.6 0 1 1 8,5 Z" fill="#fff"/><circle cx="5.5" cy="4.4" r="1" fill="var(--ink)"/></svg>18 Corvell Road, Suite 304,</li>
      <li class="address">Brisdale, NJ 07391</li>
    </ul>
  </section>

  <section class="card card--back">
    <svg class="back-art" viewBox="0 0 620 354" width="620" height="354" aria-hidden="true">
      <rect width="620" height="62" fill="var(--yellow)"/>
      <rect y="62" width="620" height="4" fill="var(--ink)"/>
      <rect y="258" width="620" height="96" fill="var(--ink)"/>
    </svg>
    <h2 class="appt-title">Appoinment</h2>
    <div class="form">
      <div class="field"><span>For:</span><span class="field__line"></span></div>
      <div class="days">
        <span class="day"><span class="box"></span>Mon</span>
        <span class="day"><span class="box"></span>Tue</span>
        <span class="day"><span class="box"></span>Wed</span>
        <span class="day"><span class="box"></span>Thu</span>
        <span class="day"><span class="box"></span>Fri</span>
        <span class="day"><span class="box"></span>Sat</span>
        <span class="day"><span class="box"></span>Sun</span>
      </div>
      <div class="field"><span>Date:</span><span class="field__line"></span><span>&nbsp;Time:</span><span class="field__line"></span></div>
    </div>
    <p class="note">If you are unable to keep your appoinment,<br>please contact us as soon as posible.</p>
    <ul class="back-contacts back-contacts--left">
      <li><svg class="icon" viewBox="0 0 11 11"><rect width="11" height="11" fill="var(--yellow)"/><path d="M3,2 L4.5,2 L5,4 L4,4.8 Q5,6.5 6.2,7 L7,6 L9,6.5 L9,8 Q5,9 2.5,4.5 Z" fill="var(--ink)"/></svg>(973) 555-0148</li>
      <li><svg class="icon" viewBox="0 0 11 11"><rect width="11" height="11" fill="var(--yellow)"/><rect x="2" y="4" width="7" height="4" fill="var(--ink)"/><rect x="3.5" y="2" width="4" height="2" fill="var(--ink)"/></svg>(973) 555.0162</li>
    </ul>
    <ul class="back-contacts back-contacts--right">
      <li>steadypmc.service@mailbox.com<svg class="icon" viewBox="0 0 11 11"><rect width="11" height="11" fill="var(--yellow)"/><rect x="2" y="3" width="7" height="5" fill="var(--ink)"/><path d="M2,3 L5.5,6 L9,3" stroke="var(--yellow)" fill="none" stroke-width=".8"/></svg></li>
      <li>www.steadypm.com<svg class="icon" viewBox="0 0 11 11"><rect width="11" height="11" fill="var(--yellow)"/><circle cx="5.5" cy="5.5" r="3.2" fill="none" stroke="var(--ink)" stroke-width="1"/><path d="M2.3,5.5 H8.7 M5.5,2.3 V8.7" stroke="var(--ink)" stroke-width=".7"/></svg></li>
    </ul>
  </section>

</main>
</body>
</html>
```